Flyer Design Project with menu

We are from Juniper Table Restaurant. We usually serve breakfast, soul food, fried and BBQ Ribs , legs, wings etc. We located at 2870 n. Harlow street, canton, 39046, MS. Since this is a new restaurant we want to let people know about us. Please create a good professional flyer including menu on that. Thank you. Please let us know if you need any other information.
Updates

Target Market(s)

We want to attract customers from 3 different locations near 15 miles radius.

Industry/Entity Type

American Restaurant

Font styles to use
Serif

Requirements
Must have
• Good graphics with food pictures.
• Soul food graphic pictures, RIBS, FISH and breakfast regular.
Nice to have
• 20% discount coupon offer.

```html
<!DOCTYPE html>
<html lang="en">
<head>
<meta charset="utf-8">
<title>Juniper Table Restaurant – Flyer and Menu</title>
<link rel="stylesheet" href="https://fonts.googleapis.com/css2?family=Alfa+Slab+One&family=Bitter:ital,wght@0,400;0,600;0,700;0,800;1,600;1,700;1,800&family=Courgette&display=swap">
<style>
  :root {
    --red: #e1262c;
    --red-dark: #c81d24;
    --yellow: #ffe53b;
    --navy: #2b3482;
    --navy-light: #3c4fa8;
    --orange: #f7941d;
    --menu-blue: #1d4ea6;
    --menu-red: #e5322a;
    --panel-grey: #dcdee2;
    --canvas: #dcdcdc;
    --white: #ffffff;
    --ink: #2a2a2a;
  }
  * { box-sizing: border-box; margin: 0; padding: 0; }
  html, body { width: 1200px; height: 810px; overflow: hidden; background: var(--canvas); }
  body { position: relative; font-family: "Bitter", Georgia, serif; }
  ul { list-style: none; }

  .page { position: absolute; top: 38px; width: 549px; height: 710px; overflow: hidden; background: var(--white); }
  .page--front { left: 35px; }
  .page--menu { left: 607px; }

  .masthead { position: absolute; left: 0; top: 0; width: 100%; height: 104px;
    background: linear-gradient(180deg, #e8262b 0%, var(--red-dark) 100%);
    border-bottom: 4px solid #e9e9e9; text-align: center; }
  .masthead__name { position: absolute; left: 0; right: 0; top: 16px;
    font-family: "Alfa Slab One", Georgia, serif; font-weight: 400; font-size: 37px; line-height: 44px;
    letter-spacing: 2px; color: var(--yellow); text-shadow: 0 2px 0 rgba(90,0,0,.35); }
  .masthead__sub { position: absolute; left: 0; right: 0; top: 62px; height: 30px;
    display: flex; align-items: center; justify-content: center; gap: 20px; color: var(--white); }
  .masthead__script { font-family: "Courgette", cursive; font-size: 24px; line-height: 30px; }
  .stars { display: flex; align-items: center; gap: 6px; }
  .stars svg { fill: var(--white); }

  /* front page */
  .hero-photo { position: absolute; left: 0; top: 108px; width: 549px; height: 300px;
    background: radial-gradient(ellipse at 55% 45%, #c7834a 0%, #a86436 30%, #e0b26a 55%, #5f6e2e 75%, #e8e2d6 100%); }
  .front-panel { position: absolute; left: 0; top: 0; width: 549px; height: 710px; }
  .front-circle { position: absolute; width: 136px; height: 136px; border-radius: 50%; border: 4px solid var(--white); }
  .front-circle--breakfast { left: 37px; top: 292px; background: radial-gradient(circle at 45% 50%, #f3c95c 0%, #d58a3a 40%, #8d3b22 75%, #e9e0c7 100%); }
  .front-circle--ribs { left: 377px; top: 292px; background: radial-gradient(circle at 55% 55%, #7a3519 0%, #5a2412 40%, #a8582c 70%, #8c7a58 100%); }
  .discount-badge { position: absolute; left: 209px; top: 294px; width: 132px; height: 132px; }
  .discount-badge svg { width: 132px; height: 132px; }
  .discount-badge__text { position: absolute; left: 0; top: 0; width: 132px; height: 132px;
    display: flex; flex-direction: column; align-items: center; justify-content: center;
    transform: rotate(-14deg); color: var(--white); font-family: "Alfa Slab One", Georgia, serif; }
  .discount-badge__pct { font-size: 36px; line-height: 36px; }
  .discount-badge__off { font-size: 21px; line-height: 24px; }

  .offer { position: absolute; top: 477px; width: 172px; text-align: center; color: var(--white); }
  .offer--breakfast { left: 18px; }
  .offer--discount { left: 188px; }
  .offer--lunch { left: 359px; }
  .offer__title { font-weight: 800; font-size: 15.5px; line-height: 19px; letter-spacing: .3px; white-space: nowrap; }
  .offer__stars { font-size: 7px; letter-spacing: 3px; line-height: 13px; margin-top: 1px; }
  .offer__text { font-weight: 700; font-size: 14px; line-height: 17.5px; white-space: nowrap; }
  .hl { color: var(--yellow); }

  .cta { position: absolute; left: 42px; top: 612px; width: 461px; height: 37px; }
  .cta__label { position: absolute; left: 0; top: 0; width: 100%; height: 100%;
    display: flex; align-items: center; justify-content: center;
    font-style: italic; font-weight: 800; font-size: 17px; color: var(--white); letter-spacing: .3px; }

  .contact { position: absolute; left: 0; width: 100%; text-align: center; color: var(--white); }
  .contact--address { top: 648px; font-weight: 700; font-size: 14px; line-height: 20px; text-transform: uppercase; }
  .contact--lines { top: 674px; font-size: 13.5px; line-height: 20px; letter-spacing: .4px;
    display: flex; justify-content: center; align-items: center; gap: 18px; }
  .contact__item { display: flex; align-items: center; gap: 5px; }
  .contact__item svg { fill: var(--yellow); }

  /* menu page */
  .menu-head { position: absolute; color: var(--menu-blue); font-weight: 800; font-size: 12.5px; line-height: 15px; white-space: nowrap; }
  .menu-head--breakfast { left: 41px; top: 137px; }
  .menu-head--lunch { left: 244px; top: 137px; }
  .menu-lead { position: absolute; color: var(--menu-red); font-style: italic; font-weight: 700; font-size: 11.5px; line-height: 15px; white-space: nowrap; }
  .menu-lead--breakfast { left: 41px; top: 153px; }
  .menu-lead--lunch { left: 244px; top: 152px; }

  .menu-list { position: absolute; color: var(--menu-blue); font-weight: 800; font-size: 8.6px; text-transform: uppercase; letter-spacing: .2px; }
  .menu-list li { height: 18.8px; line-height: 18.8px; white-space: nowrap; }
  .menu-list .cat { color: var(--menu-red); }
  .menu-list--breakfast { left: 42px; top: 192.6px; }
  .menu-list--salads { left: 45px; top: 384.6px; }
  .menu-list--burgers { left: 45px; top: 477.6px; }
  .menu-list--ribs { left: 45px; top: 564.6px; }
  .menu-list--soul { left: 244px; top: 191.6px; }
  .menu-list--soul li.two-line { height: 28px; line-height: 9.5px; padding-top: 4px; }
  .menu-list--soul li.two-line small { font-size: 8px; font-weight: 700; text-transform: none; }
  .menu-list--stick { left: 244px; top: 313px; }
  .menu-list--sides { left: 430px; top: 205.6px; }

  .sides-label { position: absolute; left: 428px; top: 184px; font-family: "Courgette", cursive; font-size: 12px; color: var(--ink); }
  .plate-note { position: absolute; left: 244px; top: 336px; color: var(--menu-red);
    font-style: italic; font-weight: 600; font-size: 10px; line-height: 13px; white-space: nowrap; }

  .combo-panel { position: absolute; left: 241px; top: 391px; width: 172px; height: 287px; }
  .combo-list { position: absolute; left: 262px; top: 408px; color: var(--menu-blue); font-weight: 800; font-size: 8.6px; text-transform: uppercase; }
  .combo-list li { height: 18.8px; line-height: 18.8px; white-space: nowrap; }
  .combo-list .cat { color: var(--menu-red); height: 9.5px; line-height: 10px; }
  .combo-list .note { color: var(--ink); font-weight: 600; text-transform: none; height: 10px; line-height: 10px; font-size: 8.5px; }
  .combo-list .gap { height: 8.5px; }

  .extra-sides { position: absolute; left: 426px; top: 462px; color: var(--menu-blue); font-weight: 800; font-size: 8.6px; text-transform: uppercase; }
  .extra-sides li { height: 18.8px; line-height: 18.8px; white-space: nowrap; }
  .extra-sides .cat { color: var(--menu-red); height: 9.5px; line-height: 10px; }
  .extra-sides .price { color: var(--ink); font-weight: 700; text-transform: none; height: 10px; line-height: 10px; font-size: 8.5px; }
  .extra-sides .price-last { color: var(--ink); font-weight: 700; text-transform: none; height: 12px; line-height: 10px; font-size: 8.5px; }
</style>
</head>
<body>

<section class="page page--front">
  <header class="masthead">
    <h1 class="masthead__name">JUNIPER TABLE</h1>
    <div class="masthead__sub">
      <span class="stars">
        <svg width="10" height="10" viewBox="0 0 24 24"><path d="M12 1l3.1 7.2 7.9.7-6 5.2 1.8 7.7L12 17.8 5.2 21.8 7 14.1 1 8.9l7.9-.7z"/></svg>
        <svg width="15" height="15" viewBox="0 0 24 24"><path d="M12 1l3.1 7.2 7.9.7-6 5.2 1.8 7.7L12 17.8 5.2 21.8 7 14.1 1 8.9l7.9-.7z"/></svg>
        <svg width="19" height="19" viewBox="0 0 24 24"><path d="M12 1l3.1 7.2 7.9.7-6 5.2 1.8 7.7L12 17.8 5.2 21.8 7 14.1 1 8.9l7.9-.7z"/></svg>
      </span>
      <span class="masthead__script">Restaurant</span>
      <span class="stars">
        <svg width="19" height="19" viewBox="0 0 24 24"><path d="M12 1l3.1 7.2 7.9.7-6 5.2 1.8 7.7L12 17.8 5.2 21.8 7 14.1 1 8.9l7.9-.7z"/></svg>
        <svg width="15" height="15" viewBox="0 0 24 24"><path d="M12 1l3.1 7.2 7.9.7-6 5.2 1.8 7.7L12 17.8 5.2 21.8 7 14.1 1 8.9l7.9-.7z"/></svg>
        <svg width="10" height="10" viewBox="0 0 24 24"><path d="M12 1l3.1 7.2 7.9.7-6 5.2 1.8 7.7L12 17.8 5.2 21.8 7 14.1 1 8.9l7.9-.7z"/></svg>
      </span>
    </div>
  </header>

  <div class="hero-photo" role="img" aria-label="Photo of a plate of grilled chicken with fries, greens and toasted bread"></div>

  <svg class="front-panel" width="549" height="710" viewBox="0 0 549 710" aria-hidden="true">
    <defs>
      <linearGradient id="panelBlue" x1="0" y1="0" x2="0" y2="1">
        <stop offset="0" stop-color="#3c4fa8"/>
        <stop offset="1" stop-color="#2b3482"/>
      </linearGradient>
    </defs>
    <path d="M0 352 Q274 302 549 348 L549 710 L0 710 Z" fill="#ffffff"/>
    <path d="M0 357 Q274 307 549 353 L549 710 L0 710 Z" fill="url(#panelBlue)"/>
    <path d="M0 648 Q274 600 549 650 L549 710 L0 710 Z" fill="#ffffff"/>
    <path d="M0 654 Q274 606 549 656 L549 710 L0 710 Z" fill="#e1262c"/>
  </svg>

  <div class="front-circle front-circle--breakfast" role="img" aria-label="Photo of a breakfast plate with biscuits, bacon and scrambled eggs"></div>
  <div class="front-circle front-circle--ribs" role="img" aria-label="Photo of barbecue ribs on a board"></div>

  <div class="discount-badge">
    <svg viewBox="0 0 120 120" aria-hidden="true">
      <g transform="translate(60 60)">
        <rect x="-46" y="-46" width="92" height="92" rx="10" fill="#ffffff"/>
        <rect x="-46" y="-46" width="92" height="92" rx="10" fill="#ffffff" transform="rotate(30)"/>
        <rect x="-46" y="-46" width="92" height="92" rx="10" fill="#ffffff" transform="rotate(60)"/>
        <rect x="-42" y="-42" width="84" height="84" rx="9" fill="#e1262c"/>
        <rect x="-42" y="-42" width="84" height="84" rx="9" fill="#e1262c" transform="rotate(30)"/>
        <rect x="-42" y="-42" width="84" height="84" rx="9" fill="#e1262c" transform="rotate(60)"/>
      </g>
    </svg>
    <div class="discount-badge__text">
      <span class="discount-badge__pct">20%</span>
      <span class="discount-badge__off">OFF</span>
    </div>
  </div>

  <div class="offer offer--breakfast">
    <h2 class="offer__title">START YOUR DAY<br>WITH US!</h2>
    <div class="offer__stars">★★★</div>
    <p class="offer__text">We open at <span class="hl">6am.</span><br>Grab a plate for only<br><span class="hl">$4.99</span> or order items<br>separately</p>
  </div>
  <div class="offer offer--discount">
    <h2 class="offer__title">ENJOY OUR 20%<br>DISCOUNT!</h2>
    <div class="offer__stars">★★★</div>
    <p class="offer__text"><span class="hl">Bring this flyer</span> with<br>you and enjoy <span class="hl">20%</span><br><span class="hl">discount</span> on your<br>order</p>
  </div>
  <div class="offer offer--lunch">
    <h2 class="offer__title">LUNCH &amp; DINNER<br>for CHAMPIONS!</h2>
    <div class="offer__stars">★★★</div>
    <p class="offer__text">Order from the Menu<br>or create a plate<br>from the line for only<br><span class="hl">$7.99</span></p>
  </div>

  <div class="cta">
    <svg width="461" height="37" viewBox="0 0 461 37" aria-hidden="true">
      <path d="M1 1 L452 1 L460 18.5 L452 36 L1 36 L8 18.5 Z" fill="#f7941d" stroke="#ffffff" stroke-width="1.5"/>
    </svg>
    <span class="cta__label">See Our Detailed Menu On The Next Page</span>
  </div>

  <p class="contact contact--address">2870 N. Harlow Street, Cedar Hollow, OH, 44890</p>
  <div class="contact contact--lines">
    <span class="contact__item">
      <svg width="14" height="10" viewBox="0 0 14 10"><path d="M0 0h14v10H0z"/><path d="M0 0l7 5 7-5" fill="none" stroke="#e1262c" stroke-width="1.2"/></svg>
      hello@junipertable.com
    </span>
    <span class="contact__item">
      <svg width="15" height="12" viewBox="0 0 15 12"><path d="M1 5c0-3 3-4 6.5-4S14 2 14 5l-3 1-1-2H5L4 6z M3 7h9l1 4H2z"/><circle cx="7.5" cy="9" r="1.4" fill="#e1262c"/></svg>
      7690 555 218
    </span>
  </div>
</section>

<section class="page page--menu">
  <header class="masthead">
    <h1 class="masthead__name">JUNIPER TABLE</h1>
    <div class="masthead__sub">
      <span class="stars">
        <svg width="10" height="10" viewBox="0 0 24 24"><path d="M12 1l3.1 7.2 7.9.7-6 5.2 1.8 7.7L12 17.8 5.2 21.8 7 14.1 1 8.9l7.9-.7z"/></svg>
        <svg width="15" height="15" viewBox="0 0 24 24"><path d="M12 1l3.1 7.2 7.9.7-6 5.2 1.8 7.7L12 17.8 5.2 21.8 7 14.1 1 8.9l7.9-.7z"/></svg>
        <svg width="19" height="19" viewBox="0 0 24 24"><path d="M12 1l3.1 7.2 7.9.7-6 5.2 1.8 7.7L12 17.8 5.2 21.8 7 14.1 1 8.9l7.9-.7z"/></svg>
      </span>
      <span class="masthead__script">Restaurant</span>
      <span class="stars">
        <svg width="19" height="19" viewBox="0 0 24 24"><path d="M12 1l3.1 7.2 7.9.7-6 5.2 1.8 7.7L12 17.8 5.2 21.8 7 14.1 1 8.9l7.9-.7z"/></svg>
        <svg width="15" height="15" viewBox="0 0 24 24"><path d="M12 1l3.1 7.2 7.9.7-6 5.2 1.8 7.7L12 17.8 5.2 21.8 7 14.1 1 8.9l7.9-.7z"/></svg>
        <svg width="10" height="10" viewBox="0 0 24 24"><path d="M12 1l3.1 7.2 7.9.7-6 5.2 1.8 7.7L12 17.8 5.2 21.8 7 14.1 1 8.9l7.9-.7z"/></svg>
      </span>
    </div>
  </header>

  <h2 class="menu-head menu-head--breakfast">START YOUR DAY WITH US!</h2>
  <p class="menu-lead menu-lead--breakfast">Breakfast starting at 6am</p>

  <ul class="menu-list menu-list--breakfast">
    <li>Eggs - 1.99</li>
    <li>Sausage patties - 2 for 1.99</li>
    <li>Smoked link sausage 2 for - 1.99</li>
    <li>Hashbrowns - 1.99</li>
    <li>Biscuits - 1.99</li>
    <li>Baked ham - 1.99</li>
    <li>Bacon - 1.99</li>
    <li>Pan cake - 1.99</li>
    <li>Sandwiches - 2.99</li>
  </ul>

  <ul class="menu-list menu-list--salads">
    <li class="cat">Salads:</li>
    <li>Chef salad - 7.00</li>
    <li>Grilled chicken salad - 7.50</li>
    <li>Popcorn chicken salad - 7.50</li>
  </ul>

  <ul class="menu-list menu-list--burgers">
    <li class="cat">Burgers:</li>
    <li>Classic burger - 5.00</li>
    <li>Classic cheeseburger - 6.00</li>
    <li>Bacon and cheeseburger - 7.00</li>
  </ul>

  <ul class="menu-list menu-list--ribs">
    <li class="cat">Ribs:</li>
    <li>Full rack - 16.99</li>
    <li>Half rack - 8.99</li>
  </ul>

  <h2 class="menu-head menu-head--lunch">LUNCH AND DINNER MENU: (Soul Food)</h2>
  <p class="menu-lead menu-lead--lunch">Order from the Menu or create a plate from<br>the line for only 7.99</p>

  <ul class="menu-list menu-list--soul">
    <li>Red beans with rice &amp; sausage</li>
    <li>Beef tips with rice</li>
    <li>Turkey necks</li>
    <li>Fried \ baked chicken</li>
    <li>Spaghetti</li>
    <li class="two-line">Stuffed bell pepper <small>(Shrimp,</small><br><small>Crab and sausage)</small></li>
  </ul>
  <ul class="menu-list menu-list--stick">
    <li>Chicken on a stick</li>
  </ul>
  <p class="plate-note">*Plate consist of an Entrée or a<br>meat, 2 sides, a bread and drink<br>of the day</p>

  <span class="sides-label">Sides</span>
  <ul class="menu-list menu-list--sides">
    <li>Rice</li>
    <li>Mac n cheese</li>
    <li>Collard greens</li>
    <li>String beans</li>
    <li>BBQ red beans</li>
    <li>Mash potatoes</li>
    <li>Corn bread</li>
    <li>Green beans</li>
    <li>Corn</li>
  </ul>

  <svg class="combo-panel" width="172" height="287" viewBox="0 0 172 287" aria-hidden="true">
    <path d="M0 0 H154 V62 L169 76 L154 90 V287 H0 Z" fill="#dcdee2"/>
  </svg>
  <ul class="combo-list">
    <li class="cat">Fried chicken</li>
    <li class="note">(Served with 2sides)</li>
    <li>2 PC white - 6.99</li>
    <li>2PC dark - 4.99</li>
    <li class="gap"></li>
    <li class="cat">Strips</li>
    <li class="note">(Served with 2sides)</li>
    <li>3PC-3.95 meal - 5.99</li>
    <li>6PC-7.00 meal - 8.99</li>
    <li>9PC-10.99 meal - 12.99</li>
    <li class="gap"></li>
    <li class="cat">Sea food</li>
    <li class="note">(Served with 2sides)</li>
    <li>2PC fried fish - 8.99</li>
    <li>6PC shrimp - 6.99</li>
    <li>12PC shrimp - 11.99</li>
  </ul>

  <ul class="extra-sides">
    <li class="cat">Sides</li>
    <li class="price">Individual - 2.00 /</li>
    <li class="price-last">Large - 4.00</li>
    <li>Okra</li>
    <li>Fries</li>
    <li>Broccoli</li>
    <li>Side salad</li>
  </ul>
</section>

</body>
</html>
```